Oriel Photography Business Card

I need a business card designed for a photography business based in Perth, Western Australia called Oriel Photography.

We specialise in wedding, event photography and portrait photography.

The business card must borrow the style of the attached logo.

The hex codes for the colours in the logo are:
#ED1D85 - Pink
#89C23E - Green
#37282F - Black

The name on the card will be:
Name: Tobrian
Phone: 0417395268
Website: www.orielphotography.example.com.au
Facebook: orielphotography

I am open and happy to accept creative concepts.

I’d like some space at the back for writing notes and appointment details.

```html
<!DOCTYPE html>
<html lang="en">
<head>
<meta charset="utf-8">
<title>Oriel Photography – Business Card</title>
<link rel="stylesheet" href="https://fonts.googleapis.com/css2?family=Arimo:wght@400;700&display=swap">
<style>
  :root {
    --card-mauve: #9b7b98;
    --pattern-pink: #b9789f;
    --pattern-green: #a39a8c;
    --band-white: #ffffff;
    --ink-dark: #37282f;
    --brand-pink: #ed1d85;
    --brand-green: #89c23e;
    --icon-blue: #2a6fb5;
    --edge-grey: #8a8a8a;
    --text-white: #ffffff;
    --text-contact: #222222;
  }
  * { box-sizing: border-box; margin: 0; padding: 0; }
  html, body {
    width: 1200px;
    height: 338px;
    overflow: hidden;
    background: #ffffff;
    font-family: "Arimo", Arial, sans-serif;
  }
  .canvas {
    position: relative;
    width: 1200px;
    height: 338px;
  }
  .card {
    position: absolute;
    top: 0;
    width: 575px;
    height: 337px;
    background: var(--card-mauve);
    border: 1px solid var(--edge-grey);
    overflow: hidden;
  }
  .card--front { left: 0; }
  .card--back { left: 624px; }

  /* Front */
  .emblem-pattern {
    position: absolute;
    left: 0; top: 0;
    width: 100%;
    height: 254px;
    background: linear-gradient(120deg,
      var(--pattern-pink) 0%,
      var(--pattern-green) 35%,
      var(--pattern-pink) 65%,
      var(--pattern-green) 100%);
  }
  .holder-name {
    position: absolute;
    left: 32px;
    top: 64px;
    font-size: 31px;
    font-weight: 700;
    color: var(--text-white);
    letter-spacing: 0.2px;
  }
  .contact-band {
    position: absolute;
    left: 0;
    top: 254px;
    width: 100%;
    height: 77px;
    background: var(--band-white);
    display: flex;
    flex-direction: column;
    align-items: center;
    justify-content: center;
    gap: 3px;
  }
  .contact-line {
    display: flex;
    align-items: center;
    gap: 10px;
    font-size: 15px;
    font-weight: 700;
    color: var(--text-contact);
    line-height: 20px;
  }
  .contact-icon { width: 18px; height: 18px; flex: none; }

  /* Back */
  .brand-mark {
    position: absolute;
    left: 230px;
    top: 27px;
    width: 116px;
    height: 116px;
    border-radius: 50%;
    background: var(--brand-pink);
    box-shadow: inset 0 0 0 14px var(--brand-green);
  }
  .brand-name {
    position: absolute;
    left: 0;
    top: 172px;
    width: 100%;
    text-align center;
    text-align: center;
    font-size: 16px;
    font-weight: 400;
    letter-spacing: 15.5px;
    padding-left: 15px;
    color: var(--ink-dark);
    text-transform: uppercase;
    white-space: nowrap;
  }
  .note-field {
    position: absolute;
    left: 52px;
    font-size: 15px;
    font-weight: 700;
    color: var(--text-white);
  }
  .note-field--notes { top: 250px; }
  .note-field--appointment { top: 292px; }
</style>
</head>
<body>
<main class="canvas">

  <section class="card card--front" aria-label="Business card front">
    <div class="emblem-pattern" role="img" aria-label="Repeating pattern of the studio emblem in pink and green"></div>
    <h1 class="holder-name">Tobrian</h1>
    <div class="contact-band">
      <p class="contact-line">
        <svg class="contact-icon" viewBox="0 0 18 18" aria-hidden="true">
          <rect width="18" height="18" rx="2" fill="var(--icon-blue)"/>
          <path d="M4 7 Q9 3 14 7 L12.5 8.5 L11 7.5 L7 7.5 L5.5 8.5 Z" fill="#fff"/>
          <rect x="5" y="9" width="8" height="5" rx="1" fill="#fff"/>
        </svg>
        <span>0417395268</span>
      </p>
      <p class="contact-line">
        <svg class="contact-icon" viewBox="0 0 18 18" aria-hidden="true">
          <circle cx="9" cy="9" r="8" fill="var(--icon-blue)"/>
        </svg>
        <span>www.orielphotography.example.com.au</span>
      </p>
      <p class="contact-line">
        <svg class="contact-icon" viewBox="0 0 18 18" aria-hidden="true">
          <rect width="18" height="18" fill="var(--icon-blue)"/>
        </svg>
        <span>orielphotography</span>
      </p>
    </div>
  </section>

  <section class="card card--back" aria-label="Business card back">
    <div class="brand-mark" aria-hidden="true"></div>
    <h2 class="brand-name">Oriel Photography</h2>
    <p class="note-field note-field--notes">Notes :</p>
    <p class="note-field note-field--appointment">Appointment :</p>
  </section>

</main>
</body>
</html>
```